Bright Harbor, LLC Business Card Design

We need a product business card designed for a new company Bright Harbor, LLC. We make and resell waterless RV cleaner, polish and protectant. It cleans and protects in a simple spray and wipe step leaving the surface protected and conditioned to repel dust, dirt, water, smudges, bugs and fingerprints while preventing fogging. Safe on acrylic, plexiglas, lexan, plastic, rubber, painted surfaces, chrome, stainless, aluminum, vinyl, leather, glass.... This is an eco-friendly green product.

We want to play off the company name to tell the consumer that the product is easy to use and associate to the nostalgics 1950's in the USA... Thinking old travel trailer with hot rod truck pulling it as the graphic, maybe the husband cleaning the truck and the wife cleaning the trailer for a Bright Harbor surface.
Updates

Just posted our newly finished logo. Need to have "Cleaner and Protectant" added to the design as well. Thanks everyone that has submitted thus far, i am working to get comments on all.

If you need a different file format, please let me know. Thank you.

Most important info, is the logo, website and the words "Cleaner" or "Clean" along "Protectant" or "Protect" the remainder is of less importance. Highlight: www.brightharborwash.example Focus is on company brand for Brighter Harbor Cleaner product: However, need a section for the following contact info: Walt Ferris (xxx) xxx-xxxx email address Would like space for QR Code if possible.

Target Market(s)

Adults in the USA between ages of 35-75 that are actively involved in the Recreational Vehicle (RV), travel trailer, and hot rod lifestyle. We are targeting the RV marked of the high end travel, 5th wheel and bus RV market. Along with hot rods, automotive and motorcycle market.

Industry/Entity Type

Travel

Requirements
Must have
• Most important info, is the logo, website and the words "Cleaner" or "Clean" along "Protectant" or "Protect" the remainder is of less importance.

Highlight:
www.brightharborwash.example

Focus is on company brand for Brighter Harbor Cleaner product: However, need a section for the following contact info:

Walt Ferris
(xxx) xxx-xxxx
email address
Nice to have
• Would like a space for a QR Code.

```html
<!DOCTYPE html>
<html lang="en">
<head>
<meta charset="utf-8">
<title>Bright Harbor, LLC — Business Card</title>
<link href="https://fonts.googleapis.com/css2?family=Ubuntu:wght@400;500;700&display=swap" rel="stylesheet">
<style>
  :root {
    --page: #e6e3de;
    --card-light: #f7f7f7;
    --card-mid: #e2e2e2;
    --card-edge: #cfcfcf;
    --accent: #f0593a;
    --ink-dark: #575757;
    --bar-gray: #5f6166;
    --white: #ffffff;
  }
  * { box-sizing: border-box; margin: 0; padding: 0; }
  html, body {
    width: 1200px; height: 891px; overflow: hidden;
    background: var(--page);
    font-family: "Ubuntu", sans-serif;
  }
  .business-card {
    position: absolute; left: 120px; top: 171px;
    width: 960px; height: 548px;
    background: radial-gradient(ellipse at 45% 35%, var(--card-light) 0%, var(--card-mid) 65%, var(--card-edge) 100%);
    box-shadow: 0 14px 30px rgba(0,0,0,.22);
    overflow: hidden;
  }
  .corner-bars { position: absolute; left: 0; top: 0; }
  .brand-name {
    position: absolute; left: 70px; top: 168px;
    font-size: 66px; font-weight: 700; letter-spacing: 3px;
    color: var(--ink-dark); text-transform: uppercase; line-height: 1;
    white-space: nowrap;
  }
  .brand-tagline {
    position: absolute; left: 74px; top: 246px;
    font-size: 20px; font-weight: 500; letter-spacing: 4px;
    color: var(--accent); text-transform: uppercase; line-height: 1;
    white-space: nowrap;
  }
  .accent-band {
    position: absolute; left: 0; top: 290px;
    width: 100%; height: 190px;
    background: var(--accent);
  }
  .band-divider { position: absolute; left: 0; top: 0; }
  .person {
    position: absolute; left: 70px; bottom: 26px;
    color: var(--white); white-space: nowrap;
  }
  .person-name { font-size: 27px; font-weight: 500; text-transform: uppercase; letter-spacing: .5px; }
  .person-role { font-size: 17px; font-weight: 400; margin-top: 3px; }
  .contact-list {
    position: absolute; left: 500px; top: 22px;
    list-style: none; color: var(--white);
    font-size: 18px; font-weight: 400; white-space: nowrap;
  }
  .contact-list li { display: flex; align-items: center; height: 29px; }
  .contact-list svg { width: 18px; height: 18px; margin-right: 12px; flex: none; }
</style>
</head>
<body>
  <div class="business-card">
    <svg class="corner-bars" width="560" height="140" viewBox="0 0 560 140" aria-hidden="true">
      <polygon points="40,52 470,52 456,68 40,68" fill="var(--bar-gray)"/>
      <polygon points="120,86 380,86 366,100 120,100" fill="var(--bar-gray)"/>
    </svg>

    <div class="brand-name">Bright Harbor</div>
    <div class="brand-tagline">Cleaner and Protectant</div>

    <div class="accent-band">
      <svg class="band-divider" width="960" height="190" viewBox="0 0 960 190" aria-hidden="true">
        <polygon points="400,0 416,0 376,190 360,190" fill="var(--white)"/>
        <polygon points="432,0 448,0 408,190 392,190" fill="var(--white)"/>
      </svg>

      <div class="person">
        <div class="person-name">Walt Ferris</div>
        <div class="person-role">Managing Director</div>
      </div>

      <ul class="contact-list">
        <li>
          <svg viewBox="0 0 18 18"><rect x="4" y="1" width="10" height="16" rx="2" fill="none" stroke="#fff" stroke-width="1.8"/><circle cx="9" cy="14" r="1" fill="#fff"/></svg>
          (555) 014 2739
        </li>
        <li>
          <svg viewBox="0 0 18 18"><path d="M4 2l3 3-2 2c1 2.5 3 4.5 5 5l2-2 3 3-2 3C7 16 2 11 1 5z" fill="#fff"/></svg>
          (555) 014 2740
        </li>
        <li>
          <svg viewBox="0 0 18 18"><rect x="1" y="4" width="16" height="11" rx="1" fill="#fff"/><path d="M1.5 4.5L9 10l7.5-5.5" fill="none" stroke="var(--accent)" stroke-width="1.5"/></svg>
          hello@brightharbor.example
        </li>
        <li>
          <svg viewBox="0 0 18 18"><circle cx="9" cy="9" r="7.5" fill="none" stroke="#fff" stroke-width="1.6"/><ellipse cx="9" cy="9" rx="3.2" ry="7.5" fill="none" stroke="#fff" stroke-width="1.3"/><path d="M1.5 9h15" stroke="#fff" stroke-width="1.3"/></svg>
          www.brightharborwash.example
        </li>
        <li>
          <svg viewBox="0 0 18 18"><path d="M9 1a5.5 5.5 0 0 0-5.5 5.5C3.5 11 9 17 9 17s5.5-6 5.5-10.5A5.5 5.5 0 0 0 9 1z" fill="#fff"/><circle cx="9" cy="6.5" r="2" fill="var(--accent)"/></svg>
          27 Lantern Quay, Bright Bay Road
        </li>
      </ul>
    </div>
  </div>
</body>
</html>
```